Brightmill Data Works

Our company is about IT hardwares and IT solutions. IT hardware such as PC, RAMS, storage and servers. IT solutions such as project management, BA. We are also selling new technology too.

Target Market(s)

Consumer, Small to Medium Business, Corporate

Requirements
Must have
• The business card must have the following:
• Name:
• Title:
• Contact Number:
• Email address:
• Website:
• Color: Must match the logo color upgrade

```html
<!DOCTYPE html>
<html lang="en">
<head>
<meta charset="UTF-8">
<title>Brightmill Data Works – Business Card</title>
<link rel="stylesheet" href="https://fonts.googleapis.com/css2?family=Saira+Semi+Condensed:wght@500;700&family=Roboto:wght@400&display=swap">
<style>
  :root {
    --backdrop: #dcdcdc;
    --card-white: #f7f7f6;
    --ink-dark: #454545;
    --ink-body: #4a4a4a;
    --brand-orange: #cf7a2c;
    --brand-orange-light: #d68d3e;
    --brand-orange-deep: #bb5f26;
    --on-orange: #ffffff;
  }
  * { margin: 0; padding: 0; box-sizing: border-box; }
  html, body { width: 1200px; height: 960px; overflow: hidden; }
  body { background: var(--backdrop); position: relative; }

  .card {
    position: absolute;
    left: 313px;
    width: 599px;
    height: 343px;
  }
  .card--front { top: 113px; background: var(--card-white); }
  .card--back {
    top: 472px;
    background: radial-gradient(ellipse 60% 75% at 50% 40%, var(--brand-orange-light) 0%, var(--brand-orange) 45%, var(--brand-orange-deep) 100%);
  }

  .brand-dot {
    position: absolute;
    border-radius: 50%;
  }
  .card--front .brand-dot {
    left: 33px; top: 42px;
    width: 260px; height: 260px;
    background: var(--brand-orange);
  }

  .wordmark {
    position: absolute;
    font-family: "Saira Semi Condensed", sans-serif;
    font-weight: 700;
    line-height: 1;
  }
  .wordmark__line { display: block; }
  .wordmark__line--main { font-size: 33px; letter-spacing: 0.5px; }
  .wordmark__line--sub { font-size: 15px; letter-spacing: 5px; margin-top: 7px; }

  .card--front .wordmark {
    right: 50px; top: 55px;
    text-align: right;
    color: var(--ink-dark);
  }
  .card--front .wordmark__line--sub { margin-right: -5px; }

  .person {
    position: absolute;
    right: 50px; top: 170px;
    text-align: right;
  }
  .person__name {
    font-family: "Saira Semi Condensed", sans-serif;
    font-weight: 500;
    font-size: 27px;
    line-height: 1;
    color: var(--ink-dark);
  }
  .person__title {
    font-family: "Roboto", sans-serif;
    font-size: 14.5px;
    color: var(--brand-orange);
    margin-top: 4px;
    letter-spacing: 0.3px;
  }

  .contact {
    position: absolute;
    right: 50px; top: 237px;
    text-align: right;
    list-style: none;
    font-family: "Roboto", sans-serif;
    font-size: 14.5px;
    line-height: 19.5px;
    color: var(--ink-body);
  }

  .card--back .brand-dot {
    left: 277px; top: 98px;
    width: 44px; height: 44px;
    background: var(--on-orange);
  }
  .card--back .wordmark {
    left: 0; right: 0; top: 184px;
    text-align: center;
    color: var(--on-orange);
  }
  .card--back .wordmark__line--main { font-size: 38px; }
  .card--back .wordmark__line--sub { font-size: 16px; letter-spacing: 6px; margin-right: -6px; }
</style>
</head>
<body>
  <section class="card card--front">
    <div class="brand-dot" aria-hidden="true"></div>
    <div class="wordmark">
      <span class="wordmark__line wordmark__line--main">BRIGHTMILL</span>
      <span class="wordmark__line wordmark__line--sub">DATA WORKS</span>
    </div>
    <div class="person">
      <div class="person__name">DANIEL HARROW</div>
      <div class="person__title">CEO/FOUNDER</div>
    </div>
    <ul class="contact">
      <li>555 014 7823</li>
      <li>daniel@brightmill.com</li>
      <li>www.brightmill.com</li>
    </ul>
  </section>

  <section class="card card--back">
    <div class="brand-dot" aria-hidden="true"></div>
    <div class="wordmark">
      <span class="wordmark__line wordmark__line--main">BRIGHTMILL</span>
      <span class="wordmark__line wordmark__line--sub">DATA WORKS</span>
    </div>
  </section>
</body>
</html>
```